Digital Marketing Website Redesign, modern, fresh, dynamic

Hi there, we would like to freshen up our website and create a new dynamic look. We are a digital marketing agency who specialise in digital transformation in the form of creating websites for appointment bookings. Our clients are service businesses such as hairdressers, dentists and doctors who's patients need to book appointments with them.

Our company name is Tallomex with the point being we can help increase your revenue curve by increasing your appointment bookings.

Our services include building the website, creating campaigns to drive traffic, increasing conversions and monitoring and reporting.

We are playing with a tagline of 'Step into your Digital Transformation' as we have a 5 step journey that customers can take with us getting them from zero to full appointment bookings.

Our current website is www.tallomex-sample.com

You can see a draft design that I mocked up on Canva here https://www.draftboard-sample.com/design/QXB82LmpR7T/KpoW39dnFsYbZet_wqe_OPa/edit?utm_content=QXB82LmpR7T&utm_campaign=designshare&utm_medium=link2&utm_source=sharebutton

Also attached some other homepage ideas. In regard to photos we are open to ideas.

Please let if you need any more information to provide us with an initial design. Thanks million and I look forward to receiving fantastic designs :)

Marian Dobbs
Tallomex

Target Market(s)

Appointment based businesses such as hairdressers, dentists, doctors

Industry/Entity Type

Marketing and Digital

Coding

Coded - Design and coding required

Number of Pages Required

1 page

Colors
0094D4
00A9DD
6FCCEA
C7EBF8
E9F6FB

Requirements
Must have
• Appointment booking CTA
Nice to have
• A website we like https://www.fergalwhitty-sample.ie

```html
<!DOCTYPE html>
<html lang="en">
<head>
<meta charset="utf-8">
<title>Tallomex — Digital Marketing</title>
<link rel="stylesheet" href="https://fonts.googleapis.com/css2?family=Ubuntu:wght@300;400;500;700&family=Open+Sans:wght@400;600;700&display=swap">
<style>
:root{
  --blue:#0094D4;
  --blue-2:#00A9DD;
  --sky:#6FCCEA;
  --ice:#C7EBF8;
  --mist:#E9F6FB;
  --heading:#0a5f8c;
  --ink:#2f3a44;
  --muted:#66717b;
  --white:#ffffff;
  --deep:#062a4a;
  --night:#0a1a2e;
}
*{margin:0;padding:0;box-sizing:border-box}
html,body{width:1200px;height:4355px;overflow:hidden}
body{position:relative;font-family:"Open Sans",sans-serif;color:var(--ink);background:var(--white)}
.abs{position:absolute}
.kicker{font-family:"Ubuntu",sans-serif;font-size:13px;color:var(--blue);text-align:center}
.kicker.line{display:inline-block;border-bottom:1px solid var(--blue);padding-bottom:3px}
.h2{font-family:"Ubuntu",sans-serif;font-weight:500;color:var(--heading);font-size:42px;text-align:center}
.btn{display:flex;align-items:center;justify-content:center;gap:12px;background:var(--blue);color:#fff;font-family:"Ubuntu",sans-serif;font-weight:500;font-size:17px;border-radius:2px;white-space:nowrap}
.btn svg{width:20px;height:20px}
.brand{font-family:"Ubuntu",sans-serif;font-weight:700;color:var(--heading)}

/* hero */
.hero{left:0;top:0;width:1200px;height:830px;background:radial-gradient(ellipse at 50% 55%,#2f8fc0 0%,#0d4f80 40%,#06223e 85%)}
.topbar{left:0;top:0;width:1200px;height:34px;color:#fff;font-size:13px;font-weight:600}
.topbar span{position:absolute;top:8px;display:flex;align-items:center;gap:6px}
.topbar svg{width:12px;height:12px;fill:#fff}
.socials{position:absolute;right:95px;top:9px;display:flex;gap:24px}
.socials i{display:block;width:13px;height:13px;border:2px solid #fff;border-radius:3px}
.nav{left:88px;top:34px;width:1027px;height:86px;background:#fff;border-radius:6px}
.nav .brand{position:absolute;left:64px;top:24px;font-size:32px}
.nav ul{position:absolute;left:275px;top:33px;list-style:none;display:flex;font-size:14px;color:var(--ink)}
.nav li:nth-child(1){margin-right:82px}.nav li:nth-child(2){margin-right:74px}.nav li:nth-child(3){margin-right:92px}.nav li:nth-child(4){margin-right:56px}.nav li:nth-child(5){margin-right:47px}
.hero-kicker{left:0;top:324px;width:1200px;text-align:center;color:#fff;font-size:14px}
.hero-title{left:0;top:345px;width:1200px;text-align:center;color:#fff;font-family:"Ubuntu",sans-serif;font-weight:300;font-size:78px;line-height:96px}
.hero .btn{position:absolute;left:490px;top:592px;width:220px;height:44px;font-size:16px}

/* services */
.services{left:0;top:744px;width:1200px;height:703px;background:var(--mist)}
.card{position:absolute;top:228px;width:324px;height:265px;background:#fff;box-shadow:0 4px 14px rgba(0,60,100,.08)}
.card .ph{position:absolute;left:18px;top:12px;width:288px;height:162px}
.card .k{position:absolute;top:194px;width:100%;text-align:center;font-size:12px;color:var(--blue)}
.card .t{position:absolute;top:210px;width:100%;text-align:center;font-family:"Ubuntu",sans-serif;font-size:26px;color:var(--heading)}
.demand{left:0;top:547px;width:1200px;text-align:center;font-size:18px;color:var(--muted)}
.outline-btn{left:468px;top:594px;width:264px;height:65px;background:#fff;box-shadow:0 3px 10px rgba(0,60,100,.08);display:flex;align-items:center;justify-content:center;gap:16px;color:var(--blue);font-family:"Ubuntu",sans-serif;font-weight:500;font-size:23px;white-space:nowrap}

/* about */
.about{left:0;top:1447px;width:1200px;height:557px;background:radial-gradient(ellipse at 75% 40%,#0d5f97 0%,#083d68 45%,var(--deep) 100%)}
.about .tilt{left:95px;top:62px;width:430px;height:390px;background:var(--blue-2);border-radius:28px;transform:rotate(5deg)}
.about .ph{left:112px;top:88px;width:382px;height:371px;border-radius:26px;background:linear-gradient(135deg,#cfd6dc,#8c969e 55%,#4f575e)}
.about .k{left:615px;top:60px;color:var(--sky);font-family:"Ubuntu",sans-serif;font-size:13px;border-bottom:1px solid var(--sky);padding-bottom:2px}
.about h2{position:absolute;left:615px;top:95px;color:#fff;font-family:"Ubuntu",sans-serif;font-weight:700;font-size:42px;line-height:52px}
.about h3{position:absolute;left:615px;top:222px;color:#fff;font-weight:600;font-size:20px}
.about p{position:absolute;left:615px;top:270px;width:495px;color:#e3eef6;font-size:12.5px;line-height:20px}
.about .btn{position:absolute;left:608px;top:429px;width:156px;height:44px;font-size:16px}

/* why */
.why{left:0;top:2004px;width:1200px;height:710px;background:#fff}
.feat{position:absolute;width:260px;font-size:13px;color:var(--muted);line-height:20px}
.feat b{display:block;font-family:"Ubuntu",sans-serif;font-weight:400;font-size:20px;color:var(--heading);line-height:26px}
.ic{position:absolute;width:64px;height:64px;border-radius:50%;background:var(--blue);display:flex;align-items:center;justify-content:center}
.ic svg{width:28px;height:28px;stroke:#fff;fill:none;stroke-width:2}

/* reviews */
.reviews{left:0;top:2714px;width:1200px;height:554px;background:linear-gradient(135deg,#1c2a36,#111b24 60%,#0a1118)}
.reviews .k{left:88px;top:51px;font-family:"Ubuntu",sans-serif;font-size:13px;color:var(--sky);border-bottom:1px solid var(--sky);padding-bottom:2px}
.reviews h2{position:absolute;left:88px;top:84px;color:#fff;font-family:"Ubuntu",sans-serif;font-weight:700;font-size:42px}
.more{left:900px;top:98px;color:#fff;font-size:15px;font-weight:600}
.more-btn{left:1066px;top:88px;width:38px;height:39px;background:var(--blue);display:flex;align-items:center;justify-content:center}
.rev{position:absolute;top:188px;width:490px;height:188px;background:rgba(120,135,150,.42);border-radius:4px;padding:30px 22px}
.rev h4{color:#fff;font-family:"Ubuntu",sans-serif;font-weight:700;font-size:26px;margin-bottom:14px}
.rev p{color:#eee;font-size:15px;line-height:24px}
.rev:after{content:"";position:absolute;left:36px;bottom:-14px;border-left:14px solid transparent;border-right:14px solid transparent;border-top:14px solid rgba(120,135,150,.42)}
.who{position:absolute;top:420px;display:flex;align-items:center;gap:20px;color:#fff}
.who .av{width:66px;height:66px;border-radius:50%;background:#c9c2bb;border:3px solid #fff}
.who b{display:block;font-family:"Ubuntu",sans-serif;font-size:22px;font-weight:500}
.who span{font-size:15px}

/* contact */
.contact{left:0;top:3268px;width:1200px;height:1025px;background:#fff}
.contact .k{left:0;top:70px;width:1200px;text-align:center}
.contact .h2{position:absolute;left:0;top:110px;width:1200px}
.footer-bg{left:0;top:552px;width:1200px;height:473px;background:linear-gradient(180deg,#06223e,#08305a 60%,#051a30)}
.form-card{left:139px;top:223px;width:921px;height:459px;background:#fff;border-radius:14px;box-shadow:0 6px 20px rgba(0,60,100,.1);overflow:hidden}
.form-card .ph{position:absolute;left:0;top:0;width:461px;height:459px;background:linear-gradient(135deg,#163a5e,#2f4a66 50%,#c27d9a)}
.form-card .brand{position:absolute;left:524px;top:60px;font-size:32px}
.form-card h3{position:absolute;left:510px;top:118px;font-family:"Ubuntu",sans-serif;font-weight:400;font-size:28px;color:var(--ink)}
.field{position:absolute;border:1px solid #cfe3ee;border-radius:3px;font-size:11px;color:#9aa0a8;padding:8px}
.send{position:absolute;left:510px;top:363px;width:360px;height:38px;background:var(--blue);color:#fff;font-size:13px;font-weight:600;display:flex;align-items:center;justify-content:center}
.f-brand{left:0;top:773px;width:1200px;text-align:center;font-size:44px;color:var(--sky)}
.f-nav{left:0;top:845px;width:1200px;display:flex;justify-content:center;gap:44px;color:#fff;font-size:14px;font-weight:600;padding-right:30px}
.f-rule{left:140px;top:912px;width:920px;height:1px;background:rgba(255,255,255,.35)}
.f-item{position:absolute;top:940px;display:flex;align-items:center;gap:16px;color:#fff;font-size:11px;line-height:16px;font-weight:600}
.f-item .o{width:56px;height:56px;border:2px solid #fff;border-radius:50%;display:flex;align-items:center;justify-content:center}
.f-item .o svg{width:26px;height:26px;stroke:#fff;fill:none;stroke-width:1.8}
.f-item b{font-size:13px;display:block}
.f-sep{position:absolute;top:935px;width:1px;height:60px;background:rgba(255,255,255,.45)}
.bottom{left:0;top:4293px;width:1200px;height:62px;background:var(--blue)}
.bottom .name{position:absolute;left:147px;top:22px;color:#fff;font-size:12px;font-weight:600}
.bottom .soc{position:absolute;right:140px;top:17px;display:flex;gap:8px}
.bottom .soc i{display:block;width:26px;height:26px;border:2px solid #fff;border-radius:3px}
</style>
</head>
<body>

<section class="abs hero" role="img" aria-label="Photo of a person walking down a glowing digital corridor">
  <div class="abs topbar">
    <span style="left:100px"><svg viewBox="0 0 24 24"><path d="M12 2a7 7 0 0 0-7 7c0 5 7 13 7 13s7-8 7-13a7 7 0 0 0-7-7zm0 9.5A2.5 2.5 0 1 1 12 6.5a2.5 2.5 0 0 1 0 5z"/></svg>48 Larkspur Lane, Brookvale</span>
    <span style="left:363px"><svg viewBox="0 0 24 24"><path d="M2 5h20v14H2z M2 5l10 8 10-8"/></svg>hello@tallomex-sample.com</span>
    <span style="left:578px"><svg viewBox="0 0 24 24"><path d="M6 2l4 5-2 3a12 12 0 0 0 6 6l3-2 5 4-3 4C10 21 3 14 2 6z"/></svg>555 - 218- 4070</span>
    <div class="socials"><i></i><i></i><i></i><i></i></div>
  </div>
  <nav class="abs nav">
    <div class="brand">Tallomex</div>
    <ul><li>Home</li><li>About Us</li><li>Services</li><li>Our team</li><li>Gallery</li><li>Contact Us</li></ul>
  </nav>
  <div class="abs hero-kicker">DIGITAL MARKETING</div>
  <h1 class="abs hero-title">Elevate Your Brand,<br>Dominate the Digital Scene</h1>
  <a class="btn">Book an Appointment <svg viewBox="0 0 24 24" fill="none" stroke="#fff" stroke-width="2.4"><path d="M4 12h15M13 6l6 6-6 6"/></svg></a>
</section>

<section class="abs services">
  <svg class="abs" style="left:0;top:-120px" width="1200" height="220" viewBox="0 0 1200 220">
    <path d="M0 140 C120 90 420 60 600 120 C780 180 900 120 1200 40 L1200 220 L0 220Z" fill="#E9F6FB"/>
    <path d="M0 150 C120 80 330 40 560 110 C420 90 200 100 40 150Z" fill="#00A9DD"/>
  </svg>
  <div class="abs" style="left:0;top:88px;width:1200px;text-align:center"><span class="kicker line">Our Services</span></div>
  <h2 class="abs h2" style="left:0;top:125px;width:1200px">Our Services</h2>
  <div class="card" style="left:85px"><div class="ph" role="img" aria-label="Photo of hands with digital marketing icons" style="background:linear-gradient(135deg,#2f3c4a,#7b8a98)"></div><div class="k">Our Services</div><div class="t">Marketing Services</div></div>
  <div class="card" style="left:436px"><div class="ph" role="img" aria-label="Photo of a laptop with booking charts" style="background:linear-gradient(135deg,#4f86b8,#c7ebf8)"></div><div class="k">Our Services</div><div class="t">Online Booking Apps</div></div>
  <div class="card" style="left:788px"><div class="ph" role="img" aria-label="Photo of a team meeting at a table" style="background:linear-gradient(135deg,#c7cdd4,#7d8a98)"></div><div class="k">Our Services</div><div class="t">Plastische Chirurgie</div></div>
  <div class="abs demand">The demanded experts in your area</div>
  <a class="abs outline-btn">Book Now <svg width="26" height="26" viewBox="0 0 24 24" fill="none" stroke="#0094D4" stroke-width="2.2"><path d="M4 12h15M13 6l6 6-6 6"/></svg></a>
</section>

<section class="abs about">
  <div class="abs tilt"></div>
  <div class="abs ph" role="img" aria-label="Photo of two colleagues looking at a computer screen"></div>
  <div class="abs k">ABOUT US</div>
  <h2>Digital Excellence,<br>Marketing Brilliance</h2>
  <h3>Where Ideas Meet Impact in the Digital Realm</h3>
  <p>Lorem ipsum dolor sit amet, consectetur adipiscing elit, sed do eiusmod tempor incididunt ut labore et dolore magna aliqua. Ut enim ad minim veniam, quis nostrud exercitation ullamco laboris nisi ut aliquip ex ea commodo consequat. Duis aute irure dolor in reprehenderit in voluptate velit esse cillum dolore eu fugiat nulla pariatur. Excepteur sint occaecat cupidatat non proident, sunt in culpa qui officia deserunt mollit.</p>
  <a class="btn">Learn More <svg viewBox="0 0 24 24" fill="none" stroke="#fff" stroke-width="2.4"><path d="M4 12h15M13 6l6 6-6 6"/></svg></a>
</section>

<section class="abs why">
  <div class="abs" style="left:0;top:67px;width:1200px;text-align:center"><span class="kicker line">WHY US</span></div>
  <h2 class="abs h2" style="left:0;top:103px;width:1200px">Why Choose Us</h2>
  <svg class="abs" style="left:0;top:0" width="1200" height="710" viewBox="0 0 1200 710">
    <circle cx="600" cy="387" r="200" fill="none" stroke="#C7EBF8" stroke-width="6"/>
    <circle cx="600" cy="387" r="182" fill="none" stroke="#0094D4" stroke-width="1.5"/>
  </svg>
  <div class="abs" role="img" aria-label="Portrait photo of a smiling businesswoman" style="left:440px;top:186px;width:320px;height:370px;border-radius:160px 160px 170px 170px;background:linear-gradient(180deg,#e9e4de,#b9a793 45%,#1c2535 70%)"></div>

  <div class="feat" style="left:90px;top:290px;text-align:right;width:245px"><b>Quality Services</b>Lorem ipsum dolor sit amet,<br>consectetur adipiscing elit,</div>
  <div class="feat" style="left:70px;top:409px;text-align:right;width:246px"><b>Expertise</b>Lorem ipsum dolor sit amet,<br>consectetur adipiscing elit,</div>
  <div class="feat" style="left:90px;top:516px;text-align:right;width:253px"><b>Client-centric</b>Lorem ipsum dolor sit amet,<br>consectetur adipiscing elit,</div>
  <div class="feat" style="left:819px;top:290px"><b>Personalized Approach</b>Lorem ipsum dolor sit amet,<br>consectetur adipiscing elit,</div>
  <div class="feat" style="left:857px;top:409px"><b>Professional</b>Lorem ipsum dolor sit amet,<br>consectetur adipiscing elit,</div>
  <div class="feat" style="left:819px;top:516px"><b>Proven Record</b>Lorem ipsum dolor sit amet,<br>consectetur adipiscing elit,</div>

  <div class="ic" style="left:410px;top:296px"><svg viewBox="0 0 24 24"><circle cx="12" cy="4" r="2"/><path d="M4 9h16M12 9v5M12 14l-4 7M12 14l4 7"/></svg></div>
  <div class="ic" style="left:385px;top:398px"><svg viewBox="0 0 24 24"><path d="M12 2v4M12 18v4M4.9 4.9l2.8 2.8M16.3 16.3l2.8 2.8M2 12h4M18 12h4M4.9 19.1l2.8-2.8M16.3 7.7l2.8-2.8"/></svg></div>
  <div class="ic" style="left:430px;top:496px"><svg viewBox="0 0 24 24"><path d="M4 14v-2a8 8 0 0 1 16 0v2"/><rect x="3" y="13" width="4" height="6" rx="1"/><rect x="17" y="13" width="4" height="6" rx="1"/></svg></div>
  <div class="ic" style="left:727px;top:296px"><svg viewBox="0 0 24 24"><circle cx="12" cy="12" r="8"/><circle cx="12" cy="12" r="4"/><circle cx="12" cy="12" r="1"/></svg></div>
  <div class="ic" style="left:750px;top:398px"><svg viewBox="0 0 24 24"><path d="M4 14v-2a8 8 0 0 1 16 0v2"/><rect x="3" y="13" width="4" height="6" rx="1"/><rect x="17" y="13" width="4" height="6" rx="1"/></svg></div>
  <div class="ic" style="left:707px;top:496px"><svg viewBox="0 0 24 24"><rect x="3" y="3" width="6" height="6"/><rect x="15" y="15" width="6" height="6"/><path d="M9 6h9v9M6 9v9h9"/></svg></div>
</section>

<section class="abs reviews" role="img" aria-label="Dark background photo of a laptop with marketing icons">
  <div class="abs k">TESTIMONIALS</div>
  <h2>Client Reviews</h2>
  <div class="abs more">More Testimonials</div>
  <div class="abs more-btn"><svg width="18" height="18" viewBox="0 0 24 24" fill="none" stroke="#fff" stroke-width="2.6"><path d="M9 5l7 7-7 7"/></svg></div>
  <div class="rev" style="left:93px"><h4>Their service was excellent</h4><p>Lorem ipsum dolor sit amet, consectetur adipiscing elit, sed do por incididunt ut labore et dolore magna aliqua. Ut enim ad mi uis nostrud exercitation</p></div>
  <div class="rev" style="left:612px"><h4>Their service was excellent</h4><p>Lorem ipsum dolor sit amet, consectetur adipiscing elit, sed do por incididunt ut labore et dolore magna aliqua. Ut enim ad mi uis nostrud exercitation</p></div>
  <div class="who" style="left:108px"><div class="av" role="img" aria-label="Client portrait photo"></div><div><b>Nora Whitfield</b><span>Client</span></div></div>
  <div class="who" style="left:628px"><div class="av" role="img" aria-label="Client portrait photo" style="background:#eadbd2"></div><div><b>Nora Whitfield</b><span>Client</span></div></div>
</section>

<section class="abs contact">
  <div class="abs footer-bg" role="img" aria-label="Dark background with network lines"></div>
  <svg class="abs" style="left:0;top:440px" width="1200" height="260" viewBox="0 0 1200 260">
    <path d="M0 140 C60 100 110 70 150 60 L150 190 C100 190 50 180 0 170Z" fill="#00A9DD"/>
    <path d="M0 155 C60 115 110 85 150 80 L150 260 L0 260Z" fill="#06223e"/>
    <path d="M1050 150 C1120 170 1170 200 1200 230 L1200 260 C1160 220 1110 195 1050 180Z" fill="#00A9DD"/>
  </svg>
  <div class="abs k"><span class="kicker line">CONTACT US</span></div>
  <h2 class="h2">Get in touch with us</h2>
  <div class="abs form-card">
    <div class="ph" role="img" aria-label="Photo of a woman with headphones working at a computer"></div>
    <div class="brand">Tallomex</div>
    <h3>Please fill out the form</h3>
    <div class="field" style="left:510px;top:173px;width:360px;height:36px">Name</div>
    <div class="field" style="left:510px;top:225px;width:173px;height:36px">Phone</div>
    <div class="field" style="left:697px;top:225px;width:173px;height:36px">Email</div>
    <div class="field" style="left:510px;top:278px;width:360px;height:70px">Message</div>
    <div class="send">Book Appointment</div>
  </div>
  <div class="abs f-brand brand" style="color:var(--sky)">Tallomex</div>
  <div class="abs f-nav"><span>HOME</span><span>SERVICES</span><span>ABOUT US</span><span>TESTIMONIALS</span><span>BLOG</span></div>
  <div class="abs f-rule"></div>
  <div class="f-item" style="left:172px"><div class="o"><svg viewBox="0 0 24 24"><circle cx="12" cy="12" r="9"/><path d="M3 12h18M12 3c3 3 3 15 0 18M12 3c-3 3-3 15 0 18"/></svg></div><div>48, Larkspur House, Larkspur Lane<br>Brookvale, State QZ 204816</div></div>
  <div class="f-sep" style="left:431px"></div>
  <div class="f-item" style="left:507px"><div class="o"><svg viewBox="0 0 24 24"><rect x="7" y="3" width="10" height="18" rx="2"/><path d="M11 18h2"/></svg></div><div><b>PHONE</b>(555) 218 4070</div></div>
  <div class="f-sep" style="left:749px"></div>
  <div class="f-item" style="left:826px"><div class="o"><svg viewBox="0 0 24 24"><rect x="3" y="6" width="18" height="12"/><path d="M3 6l9 7 9-7"/></svg></div><div><b>EMAIL</b>hello@tallomex-sample.com</div></div>
</section>

<footer class="abs bottom">
  <div class="name">Tallomex</div>
  <div class="soc"><i></i><i></i><i></i><i></i></div>
</footer>

</body>
</html>
```